BOLD & MINIMALIST DESIGN NEEDED

We want a very bold but minimalistic business card design that is impactful and utilizes both sides of the business card. Our current logo is included for your use.

We want bold fonts and good use of negative space. We don't want the logo to overpower the design.

Target Market(s)

Professionals who are building new commercial buildings.

Industry/Entity Type

Construction

Contact Information for Business Card

Name, Title, email, office phone, cell phone, website

Font styles to use
Serif
Sans Serif

Requirements
Must have
• Bold design!

```html
<!DOCTYPE html>
<html lang="en">
<head>
<meta charset="utf-8">
<title>Ridgeline Design + Build — Business Card</title>
<link rel="stylesheet" href="https://fonts.googleapis.com/css2?family=Montserrat:wght@700&family=Fira+Sans:wght@400&display=swap">
<style>
  :root {
    --stage: #1c1c1c;
    --card-dark: #161616;
    --card-light: #ffffff;
    --accent: #7cc520;
    --ink: #1a1a1a;
    --muted: #8a8a8a;
  }
  * { margin: 0; padding: 0; box-sizing: border-box; }
  html, body { width: 1200px; height: 1122px; overflow: hidden; }
  body {
    background: var(--stage);
    position: relative;
    font-family: "Fira Sans", sans-serif;
  }
  .card {
    position: absolute;
    width: 720px;
    height: 412px;
    border-radius: 30px;
    overflow: hidden;
  }
  .card--back {
    left: 400px; top: 90px;
    background: var(--card-dark);
    display: flex; align-items: center; justify-content: center;
  }
  .card--front {
    left: 80px; top: 610px;
    background: var(--card-light);
  }
  .brand {
    display: flex; align-items: center; gap: 14px;
    font-family: "Montserrat", sans-serif;
    font-weight: 700;
    letter-spacing: 0.02em;
  }
  .brand__mark { width: 22px; height: 22px; flex: none; }
  .card--back .brand { color: var(--muted); font-size: 40px; }
  .card--back .brand__mark { background: var(--muted); }
  .card--front .brand {
    position: absolute; left: 0; right: 0; top: 70px;
    justify-content: center;
    color: var(--ink); font-size: 30px;
  }
  .card--front .brand__mark { background: var(--accent); width: 18px; height: 18px; }
  .identity {
    position: absolute; right: 420px; top: 196px;
    text-align: right;
  }
  .identity__name {
    font-family: "Montserrat", sans-serif;
    font-weight: 700; font-size: 36px;
    color: var(--accent); letter-spacing: 0.01em;
  }
  .identity__role { font-size: 20px; color: var(--ink); margin-top: 4px; }
  .divider {
    position: absolute; left: 330px; top: 180px;
    width: 2px; height: 150px; background: var(--accent);
  }
  .contact {
    position: absolute; left: 360px; top: 186px;
    list-style: none;
  }
  .contact__item {
    display: flex; align-items: center; gap: 12px;
    font-size: 19px; color: var(--ink); line-height: 34px;
  }
  .contact__icon { width: 16px; height: 16px; flex: none; }
</style>
</head>
<body>
  <section class="card card--back" aria-label="Card back">
    <div class="brand"><span class="brand__mark"></span>Ridgeline Design + Build</div>
  </section>

  <section class="card card--front" aria-label="Card front">
    <div class="brand"><span class="brand__mark"></span>Ridgeline Design + Build</div>

    <div class="identity">
      <p class="identity__name">MARCUS HALE</p>
      <p class="identity__role">Founder &amp; CEO</p>
    </div>

    <div class="divider"></div>

    <ul class="contact">
      <li class="contact__item">
        <svg class="contact__icon" viewBox="0 0 16 16" aria-hidden="true"><path fill="var(--accent)" d="M3 1l3 3-1.5 2a9 9 0 0 0 5.5 5.5L12 10l3 3-2 2C7 15 1 9 1 3z"/></svg>
        (555) 214-3380
      </li>
      <li class="contact__item">
        <svg class="contact__icon" viewBox="0 0 16 16" aria-hidden="true"><rect x="4" y="1" width="8" height="14" rx="1.5" fill="none" stroke="var(--accent)" stroke-width="1.6"/><circle cx="8" cy="12.5" r="1" fill="var(--accent)"/></svg>
        (555) 214-3380
      </li>
      <li class="contact__item">
        <svg class="contact__icon" viewBox="0 0 16 16" aria-hidden="true"><rect x="1" y="3" width="14" height="10" fill="var(--accent)"/><path d="M1 3l7 6 7-6" fill="none" stroke="#fff" stroke-width="1.2"/></svg>
        info@ridgelinebuildco.com
      </li>
      <li class="contact__item">
        <svg class="contact__icon" viewBox="0 0 16 16" aria-hidden="true"><circle cx="8" cy="8" r="6.5" fill="none" stroke="var(--accent)" stroke-width="1.6"/><path d="M1.5 8h13M8 1.5c-3 3.5-3 9.5 0 13M8 1.5c3 3.5 3 9.5 0 13" fill="none" stroke="var(--accent)" stroke-width="1.2"/></svg>
        ridgelinebuildco.com
      </li>
    </ul>
  </section>
</body>
</html>
```